Single-sided business card for restaurant velmora with new logo made on this site

Business card options with new logo including restaurant name, address, phone number and website. This business card is single-sided only and will be presented at the hostess desk for clients to take. I would like to see options based on a cream card background, a white card background, a yellow card background and a burgundy colored background. It needs to be elegant and traditional.

Target Market(s)

local and international crowd

Industry/Entity Type

restaurant

Contact Information for Business Card

address, website and phone number

Font styles to use
Serif

Colors
EE7325
F08F49
F5BC92
FAE3D3
FDF4ED

Requirements
Must have
• new logo, address, phone number, website
Should not have
• more than three colors

```html
<!DOCTYPE html>
<html lang="es">
<head>
<meta charset="utf-8">
<title>Velmora – Business Card Options</title>
<link rel="stylesheet" href="https://fonts.googleapis.com/css2?family=Tinos:wght@400;700&display=swap">
<style>
  :root {
    --card-yellow: #f6b331;
    --ink: #111111;
    --paper: #ffffff;
    --crop: #c8c8c8;
  }
  * { margin: 0; padding: 0; box-sizing: border-box; }
  html, body { width: 1200px; height: 1117px; overflow: hidden; background: var(--paper); }
  .sheet {
    position: relative; width: 1200px; height: 1117px;
    font-family: "Tinos", "Times New Roman", serif;
  }
  .card-yellow {
    position: absolute; background: var(--card-yellow); color: var(--ink);
    display: flex; flex-direction: column; align-items: center; justify-content: center; text-align: center;
  }
  .card-yellow--strip { left: 45px; top: 136px; width: 509px; height: 311px; }
  .card-yellow--strip .address-line { font-weight: 700; font-size: 18.7px; margin-top: -24px; }
  .card-yellow--stack { left: 636px; top: 136px; width: 519px; height: 317px; font-size: 20.9px; line-height: 26.7px; }
  .card-yellow--stack .stack-text { margin-top: -10px; }

  .crop-marks { position: absolute; left: 0; top: 0; }

  .card-white { position: absolute; color: var(--card-yellow); }
  .brand-block { position: absolute; display: flex; flex-direction: column; align-items: center; }
  .brand-square { background: var(--card-yellow); }
  .brand-name { font-size: 24px; letter-spacing: 5px; line-height: 1; margin-top: 22px; padding-left: 5px; }

  .card-white--left .brand-block { left: 100px; top: 616px; width: 126px; }
  .card-white--left .brand-square { width: 74px; height: 74px; }
  .card-white--left .heading { position: absolute; left: 274px; top: 606px; font-size: 27px; line-height: 27.3px; white-space: nowrap; }
  .contact-list { position: absolute; left: 274px; top: 706px; list-style: none; font-size: 13.7px; line-height: 19.8px; white-space: nowrap; }
  .contact-list li { display: flex; align-items: center; gap: 6px; }
  .contact-list svg { width: 13px; height: 13px; flex: none; }

  .card-white--right .brand-block { left: 682px; top: 612px; width: 118px; }
  .card-white--right .brand-square { width: 62px; height: 62px; }
  .card-white--right .details { position: absolute; left: 831px; top: 617px; font-size: 17.3px; line-height: 26.7px; white-space: nowrap; }
</style>
</head>
<body>
<main class="sheet">

  <section class="card-yellow card-yellow--strip" aria-label="Yellow card, single-line address">
    <p class="address-line">Calle Jacaranda 417. Bahía Serena, Oaxaca CP 70999</p>
  </section>

  <section class="card-yellow card-yellow--stack" aria-label="Yellow card, stacked details">
    <div class="stack-text">
      <p>Restaurant Velmora</p>
      <p>Calle Jacaranda 417</p>
      <p>Bahía Serena, Oaxaca CP 70999</p>
      <p>Reservaciones 958-555-0142</p>
      <p>www.velmora.com.mx</p>
    </div>
  </section>

  <svg class="crop-marks" width="1200" height="1117" aria-hidden="true">
    <g stroke="var(--crop)" stroke-width="1">
      <path d="M21 527.5h57M49.5 500v55"/>
      <path d="M531 527.5h57M559.5 500v55"/>
      <path d="M613 527.5h57M641.5 500v55"/>
      <path d="M1121 527.5h57M1149.5 500v55"/>
      <path d="M21 838.5h57M49.5 811v55"/>
      <path d="M531 838.5h57M559.5 811v55"/>
      <path d="M613 838.5h57M641.5 811v55"/>
      <path d="M1121 838.5h57M1149.5 811v55"/>
    </g>
  </svg>

  <section class="card-white card-white--left" aria-label="White card, icon contact layout">
    <div class="brand-block">
      <div class="brand-square"></div>
      <p class="brand-name">VELMORA</p>
    </div>
    <h1 class="heading" style="font-weight:400">Restaurant<br>Velmora<br>Calle Jacaranda 417</h1>
    <ul class="contact-list">
      <li>
        <svg viewBox="0 0 14 14"><circle cx="7" cy="7" r="7" fill="currentColor"/><path d="M3.5 7.2 7 4l3.5 3.2H9.5v3H8V8.5H6v1.7H4.5v-3z" fill="#fff"/></svg>
        Bahía Serena, Oaxaca CP 70999
      </li>
      <li>
        <svg viewBox="0 0 14 14"><circle cx="7" cy="7" r="7" fill="currentColor"/><path d="M3.5 6.2c0-1.4 7-1.4 7 0v.8H9V6H5v1H3.5zM4.5 7.5h5l.6 2.5H3.9z" fill="#fff"/></svg>
        Reservaciones 958-555-0142
      </li>
      <li>
        <svg viewBox="0 0 14 14"><circle cx="7" cy="7" r="7" fill="currentColor"/><circle cx="7" cy="7" r="3.8" fill="none" stroke="#fff" stroke-width="1"/><path d="M3.2 7h7.6M7 3.2c-1.6 2.2-1.6 5.4 0 7.6M7 3.2c1.6 2.2 1.6 5.4 0 7.6" fill="none" stroke="#fff" stroke-width=".8"/></svg>
        www.velmora.com.mx
      </li>
    </ul>
  </section>

  <section class="card-white card-white--right" aria-label="White card, list contact layout">
    <div class="brand-block">
      <div class="brand-square"></div>
      <p class="brand-name">VELMORA</p>
    </div>
    <div class="details">
      <p>Restaurant Velmora</p>
      <p>Calle Jacaranda 417</p>
      <p>Bahía Serena, Oaxaca CP 70999</p>
      <p>Reservaciones 958-555-0142</p>
      <p>www.velmora.com.mx</p>
    </div>
  </section>

</main>
</body>
</html>
```